Salon and Spa Distributor Business Card

Need a business card. We are are distributor in the salon and spa industry. We identify with natural beauty. Need a card with:
Company Name: Petal Quarry"
Title: "President & CEO"
Address
Company Phone number
email
website
Tag Line:" Natural Beauty, Sourced Well"

Industry/Entity Type

Business

Contact Information for Business Card

Name: Dov Strommen
Title: "President & CEO"
Address: 31 Harlow Ln, Bexmoor, NJ 07813
Company Phone number: 800-463-5918
email: dovstrommen@petalquarry.example
website: www.petalquarry.example

Requirements
Should not have
• No black backgrounds

```html
<!DOCTYPE html>
<html lang="en">
<head>
<meta charset="utf-8">
<title>Petal Quarry Business Card</title>
<link href="https://fonts.googleapis.com/css2?family=Mulish:wght@300;400;600;700&display=swap" rel="stylesheet">
<style>
  :root {
    --backdrop: #efefef;
    --paper: #f6f6f5;
    --green: #3f9a35;
    --green-deep: #3a8632;
    --green-light: #56ad36;
    --ink: #7a7a7a;
    --ink-dark: #6a6a6a;
    --rule: #8cc46f;
    --on-green: #ffffff;
  }
  * { margin: 0; padding: 0; box-sizing: border-box; }
  html, body { width: 1200px; height: 900px; overflow: hidden; }
  body {
    background: var(--backdrop);
    font-family: "Mulish", sans-serif;
    position: relative;
  }
  .card {
    position: absolute;
    width: 560px;
    height: 320px;
    border-radius: 2px;
    box-shadow: 0 2px 6px rgba(0,0,0,0.12);
    overflow: hidden;
  }

  /* Back side */
  .card-back {
    left: 560px; top: 100px;
    background: linear-gradient(135deg, var(--green-deep) 0%, var(--green-light) 100%);
    color: var(--on-green);
  }
  .back-lockup {
    position: absolute;
    left: 0; right: 0; top: 112px;
    display: flex; align-items: center; justify-content: center; gap: 14px;
  }
  .back-lockup .brand-dot {
    width: 22px; height: 22px; border-radius: 50%; background: var(--on-green);
  }
  .back-lockup .brand-name {
    font-size: 40px; font-weight: 300; letter-spacing: 0.5px; line-height: 48px;
  }
  .back-tagline {
    position: absolute; left: 0; right: 0; top: 172px;
    text-align: center; font-size: 15px; font-weight: 400; letter-spacing: 0.6px;
  }

  /* Front side */
  .card-front {
    left: 80px; top: 480px;
    background: var(--paper);
  }
  .front-brand {
    position: absolute; left: 70px; top: 50px;
    display: flex; align-items: center; gap: 12px;
    color: var(--green);
  }
  .front-brand .brand-dot {
    width: 18px; height: 18px; border-radius: 50%; background: var(--green);
  }
  .front-brand .brand-name {
    font-size: 30px; font-weight: 300; line-height: 40px;
  }
  .front-rule {
    position: absolute; left: 60px; top: 128px;
    width: 390px; height: 1px; background: var(--rule);
  }
  .contact-list {
    position: absolute; left: 40px; top: 168px;
    list-style: none; color: var(--ink);
    font-size: 15px; line-height: 24px;
  }
  .contact-list li { display: flex; align-items: center; gap: 9px; }
  .contact-list svg { width: 13px; height: 13px; fill: var(--green-deep); flex: none; }
  .person {
    position: absolute; right: 40px; top: 150px;
    text-align: right;
  }
  .person-name { font-size: 21px; font-weight: 600; color: var(--green-deep); line-height: 24px; }
  .person-title { font-size: 16px; color: var(--ink); line-height: 22px; }
  .address {
    position: absolute; right: 40px; top: 216px;
    text-align: right; font-size: 15px; line-height: 21px; color: var(--ink);
    font-style: normal;
  }
  .address .company { font-weight: 700; color: var(--ink-dark); }
  .edge-tab {
    position: absolute; right: -8px; top: 160px;
    width: 20px; height: 44px; border-radius: 6px;
    background: var(--green-deep);
  }
</style>
</head>
<body>

<section class="card card-back" aria-label="Card back">
  <div class="back-lockup">
    <span class="brand-dot"></span>
    <span class="brand-name">Petal Quarry</span>
  </div>
  <p class="back-tagline">Natural Beauty, Sourced Well</p>
</section>

<section class="card card-front" aria-label="Card front">
  <div class="front-brand">
    <span class="brand-dot"></span>
    <span class="brand-name">Petal Quarry</span>
  </div>
  <div class="front-rule"></div>

  <ul class="contact-list">
    <li>
      <svg viewBox="0 0 16 16" aria-hidden="true"><path d="M3.5 1l2.5 3-1.5 1.6c.8 1.9 2.3 3.4 4.3 4.4L10.4 8.5l3.1 2.4-1.4 3.1C6.8 13.6 2.3 9.2 1.6 3z"/></svg>
      800 463 5918
    </li>
    <li>
      <svg viewBox="0 0 16 16" aria-hidden="true"><path d="M1 3h14v10H1z M1.5 3.5L8 9l6.5-5.5" stroke="#f6f6f5" stroke-width="1"/></svg>
      dovstrommen@petalquarry.example
    </li>
    <li>
      <svg viewBox="0 0 16 16" aria-hidden="true"><circle cx="8" cy="8" r="7"/><path d="M1 8h14M8 1c-3 3.5-3 10.5 0 14M8 1c3 3.5 3 10.5 0 14" stroke="#f6f6f5" stroke-width="1" fill="none"/></svg>
      www.petalquarry.example
    </li>
  </ul>

  <div class="person">
    <p class="person-name">Dov Strommen</p>
    <p class="person-title">President &amp; CEO</p>
  </div>
  <div class="edge-tab"></div>

  <address class="address">
    <span class="company">Petal Quarry</span><br>
    31 Harlow Ln<br>
    Bexmoor, NJ 07813
  </address>
</section>

</body>
</html>
```